EXCITING DECK for Automotive dealers that shows how our Technology works.

General Concept
The deck should visually represent the Trade and Credit Lead Life Cycle program is a dynamic, interconnected journey, illustrating how leads are generated, nurtured, and converted. The focus should be on how your system flows seamlessly between credit and trade-in opportunities for consumers, with the goal of maximizing engagement and conversions.
Slide 1: Title Slide - Lead Life Cycle Program
• Visual Concept: A stylized cycle or wheel that represents the stages of the lead life cycle, with arrows connecting each stage.
• Headline: "Lead Life Cycle Program"
• Subhead line: "Credit Pre-Qualification and Trade-In Appraisal"
• Imagery: Modern, sleek graphics of vehicles, smartphones (for texting), email icons, and dollar signs for value.
Slide 2: Lead Generation Sources
• Visual Concept: A funnel with the top representing the different lead generation sources.
• Content:
o Top of Funnel (Leads Enter):
 Pre-Qualification Tool (Fast4Loan)- How it Works
 1. Converts Web Traffic into the highest quality lead on the market
 Vorqel Email/Mail Marketing – How it Works
 1. Delivers actionable leads from email marketing not Just OPENS AND CLICKS. Show the text demo. Audiences below
1. Past Sold Customers (Equity Targets)
2. Past Service Onlu Department Customers (Conquest Sales)
3. Unsold Leads (from previous interactions)
o Each source should have a distinct icon to represent it (e.g., envelope for email, a wrench for past service customers, etc.).
• Headline: "Multiple Lead Sources Feeding into the Program"
• Imagery: The funnel narrowing toward the next step with leads symbolized by icons flowing downward.
Slide 3: Credit Leads - Pre-Qualified Flow
• Visual Concept: A customer engaging with the Fast4Loan tool on their mobile, being pre-qualified, and then us sending a offer to appraise their trade.
• Flow Explanation:
o Customer pre-qualifies via Fast4Loan → Receives credit approval → Email and Mail Example to check trade-in value.
• Headline: "Pre-Qualified Leads: Offering Trade-In Appraisal"
• Imagery: A sequence that shows how a customer moves from pre-qualification to considering their trade-in value. To purchasing
Slide 4: Trade-In Leads - Valuation Flow
• Visual Concept: A customer who has received a trade-in valuation offer now being prompted to pre-qualify for financing.
• Flow Explanation:
o Customer texts for vehicle value → Receives trade-in appraisal → Offer to pre-qualify for financing appears link is at the bottom of the text response.
• Headline: "Trade-In Leads: Offering Credit Pre-Qualification"
• Imagery: A customer looking at their trade-in value on their phone and being shown an additional prompt to pre-qualify for a loan.
Slide 5: Cross-Offer Opportunities
• Visual Concept: A two-way street or cycle, illustrating the seamless transition between offering pre-qualification to trade-in customers and offering trade-in value to credit leads.
• Content:
o Two pathways:
1. Start as a Credit Lead → Offer Trade-In Valuation
2. Start as a Trade-In Lead → Offer Credit Pre-Qualification
o Headline: "Cross-Offer Opportunities for Maximum Engagement"
• Imagery: Arrows going in both directions, symbolizing the back-and-forth opportunities between credit and trade leads.
Digital Retargeting for Cross-Action Engagement
• Visual Concept: An omnichannel approach with a customer in the center, surrounded by email/Mail icons, Chatterbook, and Snapgrove logos. Arrows leading from each platform back to the customer, showing how these channels drive engagement.
• Content:
o Title: "Engage to Convert one lead type to get both with Email/Mail and Digital Retargeting"
o Explanation:
 Whether a lead starts as a Pre-Qualified Credit Lead or a Trade-In Valuation Lead, we use personalized Email/Mail Campaigns and Digital Retargeting Ads (Chatterbook & Snapgrove) to encourage them to take the next action.
 If they pre-qualify for credit, we retarget them with trade-in valuation offers.
 If they start with a trade-in valuation, we follow up with financing offers.
o Headline: "Leverage Email & Social Retargeting to Drive Cross-Action"
• Visuals:
o Icons of Email, Chatterbook, and Snapgrove: Showing the platforms through which you retarget leads.
o Customer Journey Map: Illustrating how leads who interacted once are guided to the next step (credit lead → trade-in offer, trade-in lead → pre-qualification).
o Arrows Flowing Between Channels: Showing how no matter where a lead starts, they are continually engaged through digital touchpoints until they complete both actions.
o Ad examples
• Call to Action: "Stay Top of Mind and Convert Leads into Multi-Action Customers"
This slide emphasizes how you’re leveraging both email/mail marketing and social media retargeting to move leads further along the customer journey, regardless of how they entered your funnel. The visuals should reinforce the idea of continuous engagement and omnipresent reminders for them to take action.
________________________________________
Slide 6: Lifecycle Representation
• Visual Concept: A circular diagram showing how leads can continuously move between credit and trade offers throughout their lifecycle.
• Content:
o Show how the lifecycle doesn’t end after one interaction, but can continue with follow-up offers.
o Headline: "Continuous Engagement Throughout the Lead Life Cycle"
• Imagery: Circular arrows or flowchart representing each stage looping back into the lifecycle, emphasizing that leads can be re-engaged.
Slide 7: Lead Conversion Goals
• Visual Concept: A progression from leads to successful transactions (e.g., a customer with keys to a new car). Showing that getting customers to take both of these actions delives a lead that is very committed to the process of buying.
• Content:
o End goal: Convert both credit and trade leads into sales.
o Show statistics or success metrics as optional data points.
o Headline: "Converting Leads into Sales"
• Imagery: A car dealership handing over keys, happy customers, and sold vehicles.
Slide 8: Next Steps / Call to Action
• Visual Concept: A final slide summarizing the key takeaways and next steps.
• Headline: "Maximize Lead Potential with Cross-Offer Opportunities"
• Imagery: A mix of credit leads, trade leads, and successful customer outcomes.
________________________________________These slides should be clean and modern, using simple but impactful visuals like arrows, icons, and flow diagrams to represent the journey. The key is to emphasize flow and interaction between credit and trade-in opportunities, showing the two-way cross-sell nature of your Lead Life Cycle Program.

I have attached a current deck so you can pull some basic product info and graphics into the new deck (PLEASE DONT JUST COPY THE OLD DECK). I have also included some of our email artwrok if you need it. If you want to look at our website go here www.plorvenadsgroup.example

Target Market(s)

Car Dealers

Industry/Entity Type

Automotive Marketing

Requirements
Must have
• PLEASE READ THE PROJECT DESCRIPTION
Nice to have
Should not have
• PLEASE dont just copy the deck i uploaded. I am looking for a differnt take.

```html
<!DOCTYPE html>
<html lang="en">
<head>
<meta charset="utf-8">
<title>Lead Life Cycle Program – Deck Overview</title>
<link rel="stylesheet" href="https://fonts.googleapis.com/css2?family=Cinzel:wght@500;600&family=Roboto:wght@400;500;700&display=swap">
<style>
  :root{
    --page:#bdbdbd;
    --slide-a:#f4f4f4;
    --slide-b:#e6e6e6;
    --red:#e0001b;
    --dark:#3a3a3c;
    --ink:#2b2b2b;
    --muted:#555;
    --white:#fff;
    --orange:#e08a12;
    --green:#8cc63f;
  }
  html,body{margin:0;padding:0;}
  body{width:1200px;height:1082px;overflow:hidden;background:var(--page);position:relative;font-family:"Roboto",Arial,sans-serif;}
  .slide{position:absolute;width:545px;height:306px;display:block;}
  .col-left{left:37.5px;}
  .col-right{left:617.8px;}
  .row-1{top:44.6px;}
  .row-2{top:387px;}
  .row-3{top:729.6px;}
  .serif{font-family:"Cinzel",Georgia,serif;font-weight:600;fill:var(--ink);}
  .sans{font-family:"Roboto",Arial,sans-serif;}
  .brand{font-family:"Roboto",Arial,sans-serif;font-weight:500;fill:var(--dark);letter-spacing:2px;}
  .subhead{font-family:"Roboto",Arial,sans-serif;font-weight:700;fill:var(--red);font-size:19px;}
  .step{font-family:"Roboto",Arial,sans-serif;font-weight:500;fill:var(--ink);font-size:14px;}
  .body-sm{font-family:"Roboto",Arial,sans-serif;font-weight:400;fill:var(--muted);font-size:11px;}
  .foot{font-family:"Roboto",Arial,sans-serif;font-weight:400;fill:var(--white);font-size:12px;}
  .icon-red{fill:var(--red);}
</style>
</head>
<body>

<svg width="0" height="0" style="position:absolute">
  <defs>
    <linearGradient id="slideBg" x1="0" y1="0" x2="1" y2="1">
      <stop offset="0" stop-color="#f7f7f7"/>
      <stop offset="0.5" stop-color="#ebebeb"/>
      <stop offset="1" stop-color="#f2f2f2"/>
    </linearGradient>
    <filter id="soft" x="-30%" y="-30%" width="160%" height="160%">
      <feDropShadow dx="0" dy="3" stdDeviation="4" flood-color="#000" flood-opacity="0.18"/>
    </filter>
    <symbol id="footer" viewBox="0 0 916 33">
      <polygon points="0,0 457,0 442,33 0,33" fill="#3a3a3c"/>
      <polygon points="477,0 916,0 916,33 459,33" fill="#e0001b"/>
    </symbol>
    <symbol id="ico-person" viewBox="0 0 40 40">
      <circle cx="20" cy="14" r="6" fill="none" stroke="#e0001b" stroke-width="3"/>
      <path d="M9 30c2-6 6-9 11-9s9 3 11 9" fill="none" stroke="#e0001b" stroke-width="3"/>
      <path d="M6 20a14 14 0 0 1 24-10M34 20a14 14 0 0 1-24 10" fill="none" stroke="#e0001b" stroke-width="2"/>
    </symbol>
    <symbol id="ico-phone" viewBox="0 0 40 40">
      <rect x="12" y="5" width="17" height="30" rx="3" fill="#e0001b"/>
      <rect x="15" y="9" width="11" height="20" fill="#fff"/>
      <path d="M8 16h8v14H8z" fill="#e0001b"/>
    </symbol>
    <symbol id="ico-coins" viewBox="0 0 40 40">
      <ellipse cx="15" cy="12" rx="9" ry="3.5" fill="#e0001b"/>
      <rect x="6" y="12" width="18" height="16" fill="#e0001b"/>
      <path d="M6 17h18M6 22h18" stroke="#fff" stroke-width="1.5"/>
      <circle cx="26" cy="26" r="9" fill="#e0001b" stroke="#fff" stroke-width="2"/>
      <text x="26" y="31" text-anchor="middle" font-family="Roboto,Arial,sans-serif" font-size="13" font-weight="700" fill="#fff">$</text>
    </symbol>
    <symbol id="ico-mail" viewBox="0 0 40 40">
      <rect x="5" y="10" width="30" height="21" fill="#e0001b"/>
      <path d="M5 10l15 12 15-12M5 31l11-10M35 31l-11-10" fill="none" stroke="#fff" stroke-width="2"/>
    </symbol>
    <symbol id="ico-car" viewBox="0 0 40 40">
      <path d="M7 20l4-9h18l4 9v10H7z" fill="#e0001b"/>
      <rect x="13" y="13" width="14" height="6" fill="#fff"/>
      <circle cx="12" cy="25" r="2.5" fill="#fff"/>
      <circle cx="28" cy="25" r="2.5" fill="#fff"/>
      <rect x="8" y="30" width="5" height="4" fill="#e0001b"/>
      <rect x="27" y="30" width="5" height="4" fill="#e0001b"/>
    </symbol>
  </defs>
</svg>

<!-- Slide 01: Title -->
<svg class="slide col-left row-1" viewBox="0 0 916 515" role="group" aria-label="Slide 1 Lead Life Cycle Program">
  <rect width="916" height="515" fill="url(#slideBg)"/>
  <g class="logo">
    <rect x="87" y="52" width="14" height="14" fill="var(--red)"/>
    <text x="108" y="65" class="brand" font-size="17">PLORVEN ADS</text>
  </g>
  <text x="86" y="218" class="serif" font-size="34">LEAD LIFE</text>
  <text x="86" y="257" class="serif" font-size="34">CYCLE PROGRAM</text>
  <rect x="86" y="275" width="298" height="3" fill="var(--red)"/>
  <text x="86" y="306" class="sans" font-size="19" fill="#333">Credit Pre-Qualification and</text>
  <text x="86" y="335" class="sans" font-size="19" fill="#333">Trade-In Appraisal</text>

  <circle cx="632" cy="255" r="155" fill="none" stroke="var(--dark)" stroke-width="26"/>
  <circle cx="632" cy="255" r="142" fill="var(--white)"/>
  <circle cx="632" cy="255" r="133" fill="none" stroke="var(--red)" stroke-width="3"/>
  <rect x="570" y="240" width="12" height="12" fill="var(--red)"/>
  <text x="588" y="252" class="brand" font-size="16">PLORVEN ADS</text>

  <g filter="url(#soft)">
    <circle cx="502" cy="165" r="43" fill="#fff"/>
    <circle cx="761" cy="165" r="43" fill="#fff"/>
    <circle cx="502" cy="348" r="43" fill="#fff"/>
    <circle cx="761" cy="348" r="43" fill="#fff"/>
  </g>
  <use href="#ico-car" x="480" y="143" width="44" height="44"/>
  <use href="#ico-phone" x="739" y="143" width="44" height="44"/>
  <text x="502" y="366" text-anchor="middle" class="sans" font-size="46" font-weight="500" fill="var(--red)">$</text>
  <use href="#ico-mail" x="737" y="324" width="48" height="48"/>

  <use href="#footer" x="0" y="482" width="916" height="33"/>
  <text x="86" y="502" class="foot">© Copyrights 2024 | All Rights Reserved</text>
  <text x="774" y="502" class="foot">Page No : 01</text>
</svg>

<!-- Slide 04: Trade-In Leads -->
<svg class="slide col-right row-1" viewBox="0 0 916 515" role="group" aria-label="Slide 4 Trade-In Leads">
  <rect width="916" height="515" fill="url(#slideBg)"/>
  <rect x="69" y="29" width="14" height="14" fill="var(--red)"/>
  <text x="90" y="42" class="brand" font-size="17">PLORVEN ADS</text>
  <text x="836" y="52" text-anchor="end" class="serif" font-size="24">TRADE-IN LEADS:</text>
  <rect x="538" y="64" width="298" height="3" fill="var(--red)"/>
  <text x="836" y="97" text-anchor="end" class="subhead">Offering Credit Pre-Qualification</text>

  <g fill="#fff" stroke="var(--red)" stroke-width="3">
    <circle cx="109" cy="168" r="33"/>
    <circle cx="109" cy="270" r="33"/>
    <circle cx="109" cy="374" r="33"/>
  </g>
  <use href="#ico-person" x="91" y="150" width="36" height="36"/>
  <use href="#ico-phone" x="91" y="252" width="36" height="36"/>
  <use href="#ico-coins" x="91" y="356" width="36" height="36"/>
  <g stroke="var(--dark)" stroke-width="2" fill="none">
    <path d="M109 208v20M103 222l6 7 6-7"/>
    <path d="M109 310v20M103 324l6 7 6-7"/>
  </g>
  <text x="162" y="173" class="step">Customer texts for vehicle value</text>
  <text x="162" y="276" class="step">Receives trade-in appraisal</text>
  <text x="162" y="378" class="step">Offer to pre-qualify for financing</text>
  <text x="162" y="398" class="step">appears</text>

  <rect x="451" y="129" width="385" height="288" rx="8" fill="var(--dark)"/>
  <rect x="457" y="129" width="379" height="288" rx="8" fill="#c9d3dc" role="img" aria-label="Photo: customer holding a phone with a loan pre-qualify offer beside a laptop showing a credit score"/>
  <g filter="url(#soft)">
    <path d="M565 140h170v35H585l-12 9 2-9h-10z" fill="#fff"/>
  </g>
  <text x="650" y="163" text-anchor="middle" class="step" font-size="14">Pre-qualify for a loan</text>

  <use href="#footer" x="0" y="482" width="916" height="33"/>
  <text x="86" y="502" class="foot">© Copyrights 2024 | All Rights Reserved</text>
  <text x="774" y="502" class="foot">Page No : 04</text>
</svg>

<!-- Slide 02: Lead Generation Sources -->
<svg class="slide col-left row-2" viewBox="0 0 916 515" role="group" aria-label="Slide 2 Lead Generation Sources">
  <rect width="916" height="515" fill="url(#slideBg)"/>
  <rect x="69" y="29" width="14" height="14" fill="var(--red)"/>
  <text x="90" y="42" class="brand" font-size="17">PLORVEN ADS</text>
  <text x="836" y="52" text-anchor="end" class="serif" font-size="24">LEAD GENERATION SOURCES</text>
  <rect x="538" y="62" width="298" height="3" fill="var(--red)"/>

  <path d="M320 118Q458 100 596 118L566 188Q458 200 350 188Z" fill="#b31e33"/>
  <ellipse cx="458" cy="118" rx="138" ry="14" fill="#c8283f"/>
  <text x="458" y="161" text-anchor="middle" class="sans" font-size="15" font-weight="700" fill="#fff">Pre-Qualification Tool</text>

  <path d="M356 224Q458 210 560 224L536 300Q458 312 380 300Z" fill="#d98410"/>
  <ellipse cx="458" cy="224" rx="102" ry="10" fill="#e9a02a"/>
  <text x="458" y="261" text-anchor="middle" class="sans" font-size="14" font-weight="700" fill="#fff">Vorqel Email/</text>
  <text x="458" y="280" text-anchor="middle" class="sans" font-size="14" font-weight="700" fill="#fff">Mail Marketing</text>

  <path d="M394 326Q457 316 520 326L504 396Q457 406 410 396Z" fill="#7cb52e"/>
  <ellipse cx="457" cy="326" rx="63" ry="9" fill="#9ad24a"/>
  <rect x="443" y="362" width="30" height="20" fill="#fff"/>
  <path d="M443 362l15 11 15-11" fill="none" stroke="#7cb52e" stroke-width="2"/>

  <text x="286" y="159" text-anchor="end" class="sans" font-size="11.5" font-weight="500" fill="var(--ink)">Converts Web Traffic into the highest</text>
  <text x="286" y="176" text-anchor="end" class="sans" font-size="11.5" font-weight="500" fill="var(--ink)">quality lead on the market</text>
  <line x1="298" y1="159" x2="330" y2="159" stroke="var(--red)" stroke-width="1"/>
  <circle cx="298" cy="159" r="3.5" fill="var(--red)"/>

  <text x="595" y="226" class="sans" font-size="11.5" font-weight="500" fill="var(--ink)">Delivers actionable leads from email marketing</text>
  <text x="595" y="243" class="sans" font-size="11.5" font-weight="500" fill="var(--ink)">not Just OPENS AND CLICKS. Show the text</text>
  <text x="595" y="260" class="sans" font-size="11.5" font-weight="500" fill="var(--ink)">demo. Audiences below</text>
  <line x1="560" y1="261" x2="581" y2="261" stroke="var(--orange)" stroke-width="1"/>
  <circle cx="581" cy="261" r="3.5" fill="var(--orange)"/>
  <g fill="none" stroke="var(--orange)" stroke-width="1.8">
    <path d="M596 278l3 3 5-6"/>
    <path d="M596 295l3 3 5-6"/>
    <path d="M596 312l3 3 5-6"/>
  </g>
  <text x="614" y="282" class="sans" font-size="10" fill="var(--ink)">Past Sold Customers</text>
  <text x="614" y="299" class="sans" font-size="10" fill="var(--ink)">Past Service Onlu Department Customers</text>
  <text x="614" y="316" class="sans" font-size="10" fill="var(--ink)">Unsold Leads</text>

  <text x="459" y="421" text-anchor="middle" class="step">Multiple Lead Sources</text>
  <text x="459" y="440" text-anchor="middle" class="step">Feeding into the Program</text>

  <use href="#footer" x="0" y="482" width="916" height="33"/>
  <text x="86" y="502" class="foot">© Copyrights 2024 | All Rights Reserved</text>
  <text x="774" y="502" class="foot">Page No : 02</text>
</svg>

<!-- Slide 05: Lifecycle Representation -->
<svg class="slide col-right row-2" viewBox="0 0 916 515" role="group" aria-label="Slide 5 Lifecycle Representation">
  <rect width="916" height="515" fill="url(#slideBg)"/>
  <rect x="69" y="29" width="14" height="14" fill="var(--red)"/>
  <text x="90" y="42" class="brand" font-size="17">PLORVEN ADS</text>
  <text x="836" y="52" text-anchor="end" class="serif" font-size="24">LIFECYCLE REPRESENTATION</text>
  <rect x="538" y="64" width="298" height="3" fill="var(--red)"/>
  <text x="836" y="97" text-anchor="end" class="subhead">Continuous Engagement Throughout the Lead Life Cycle</text>

  <g fill="none" stroke-width="22">
    <path d="M480.6 146A130 130 0 0 1 587.5 262.7" stroke="var(--red)"/>
    <path d="M586 296.6A130 130 0 0 1 469.3 403.5" stroke="var(--dark)"/>
    <path d="M435.4 402A130 130 0 0 1 328.5 285.3" stroke="var(--red)"/>
    <path d="M330 251.4A130 130 0 0 1 446.7 144.5" stroke="var(--dark)"/>
  </g>
  <circle cx="458" cy="274" r="102" fill="var(--white)" filter="url(#soft)"/>
  <rect x="396" y="263" width="12" height="12" fill="var(--red)"/>
  <text x="414" y="275" class="brand" font-size="16">PLORVEN ADS</text>

  <circle cx="306" cy="161" r="6" fill="#fff" stroke="var(--dark)" stroke-width="3"/>
  <circle cx="597" cy="161" r="6" fill="#fff" stroke="var(--red)" stroke-width="3"/>
  <circle cx="306" cy="347" r="6" fill="#fff" stroke="var(--red)" stroke-width="3"/>
  <circle cx="597" cy="347" r="6" fill="#fff" stroke="var(--dark)" stroke-width="3"/>

  <text x="285" y="166" text-anchor="end" class="step" font-size="17">Lorem ipsum dolor</text>
  <text x="285" y="191" text-anchor="end" class="body-sm">Lorem ipsum dolor sit amet, consectetur</text>
  <text x="285" y="208" text-anchor="end" class="body-sm">adipiscing elit, sed do eiusmod</text>

  <text x="617" y="166" class="step" font-size="17">Lorem ipsum dolor</text>
  <text x="617" y="191" class="body-sm">Lorem ipsum dolor sit amet, consectetur</text>
  <text x="617" y="208" class="body-sm">adipiscing elit, sed do eiusmod</text>

  <text x="285" y="352" text-anchor="end" class="step" font-size="17">Lorem ipsum dolor</text>
  <text x="285" y="377" text-anchor="end" class="body-sm">Lorem ipsum dolor sit amet, consectetur</text>
  <text x="285" y="394" text-anchor="end" class="body-sm">adipiscing elit, sed do eiusmod</text>

  <text x="617" y="352" class="step" font-size="17">Lorem ipsum dolor</text>
  <text x="617" y="377" class="body-sm">Lorem ipsum dolor sit amet, consectetur</text>
  <text x="617" y="394" class="body-sm">adipiscing elit, sed do eiusmod</text>

  <use href="#footer" x="0" y="482" width="916" height="33"/>
  <text x="86" y="502" class="foot">© Copyrights 2024 | All Rights Reserved</text>
  <text x="774" y="502" class="foot">Page No : 05</text>
</svg>

<!-- Slide 03: Pre-Qualified Leads -->
<svg class="slide col-left row-3" viewBox="0 0 916 515" role="group" aria-label="Slide 3 Pre-Qualified Leads">
  <rect width="916" height="515" fill="url(#slideBg)"/>
  <rect x="69" y="29" width="14" height="14" fill="var(--red)"/>
  <text x="90" y="42" class="brand" font-size="17">PLORVEN ADS</text>
  <text x="836" y="52" text-anchor="end" class="serif" font-size="24">PRE-QUALIFIED LEADS</text>
  <rect x="538" y="64" width="298" height="3" fill="var(--red)"/>
  <text x="836" y="97" text-anchor="end" class="subhead">Offering Trade-In Appraisal</text>

  <rect x="68" y="128" width="375" height="289" rx="8" fill="#7d8a93" role="img" aria-label="Photo: hand tapping a smartphone showing a trade-in value offer"/>
  <g filter="url(#soft)">
    <path d="M329 140h143v33H346l-12 9 2-9h-7z" fill="#fff"/>
  </g>
  <text x="400" y="162" text-anchor="middle" class="step" font-size="14">Pre-Qualified</text>

  <g fill="#fff" stroke="var(--red)" stroke-width="3">
    <circle cx="521" cy="168" r="33"/>
    <circle cx="521" cy="270" r="33"/>
    <circle cx="521" cy="373" r="33"/>
  </g>
  <use href="#ico-person" x="503" y="150" width="36" height="36"/>
  <use href="#ico-phone" x="503" y="252" width="36" height="36"/>
  <use href="#ico-mail" x="503" y="355" width="36" height="36"/>
  <g stroke="var(--dark)" stroke-width="2" fill="none">
    <path d="M521 208v20M515 222l6 7 6-7"/>
    <path d="M521 310v20M515 324l6 7 6-7"/>
  </g>
  <text x="574" y="173" class="step">Customer pre-qualifies via Fast4Loan</text>
  <text x="574" y="275" class="step">Receives credit approval</text>
  <text x="574" y="378" class="step">Email and Mail</text>

  <use href="#footer" x="0" y="482" width="916" height="33"/>
  <text x="86" y="502" class="foot">© Copyrights 2024 | All Rights Reserved</text>
  <text x="774" y="502" class="foot">Page No : 03</text>
</svg>

<!-- Slide 06: Lead Conversion Goals -->
<svg class="slide col-right row-3" viewBox="0 0 916 515" role="group" aria-label="Slide 6 Lead Conversion Goals">
  <rect width="916" height="515" fill="url(#slideBg)"/>
  <rect x="69" y="29" width="14" height="14" fill="var(--red)"/>
  <text x="90" y="42" class="brand" font-size="17">PLORVEN ADS</text>
  <text x="836" y="52" text-anchor="end" class="serif" font-size="24">LEAD CONVERSION GOALS</text>
  <rect x="538" y="64" width="298" height="3" fill="var(--red)"/>
  <text x="836" y="97" text-anchor="end" class="subhead">Converting Leads into Sales</text>

  <rect x="61" y="321" width="155" height="119" fill="var(--red)"/>
  <rect x="71" y="116" width="410" height="315" fill="#6b6f76" role="img" aria-label="Photo: dealership staff handing car keys to a happy customer at a desk"/>

  <g fill="none" stroke="var(--dark)" stroke-width="10" transform="rotate(-90 584 183)">
    <circle cx="584" cy="183" r="38" stroke-dasharray="59.7 300"/>
  </g>
  <g fill="none" stroke="var(--dark)" stroke-width="10" transform="rotate(-90 762 183)">
    <circle cx="762" cy="183" r="38" stroke-dasharray="119.4 300"/>
  </g>
  <g fill="none" stroke="var(--dark)" stroke-width="10" transform="rotate(-90 584 341)">
    <circle cx="584" cy="341" r="38" stroke-dasharray="179.1 300"/>
  </g>
  <circle cx="762" cy="341" r="38" fill="none" stroke="var(--dark)" stroke-width="10"/>
  <g fill="#fff" filter="url(#soft)">
    <circle cx="584" cy="183" r="31"/>
    <circle cx="762" cy="183" r="31"/>
    <circle cx="584" cy="341" r="31"/>
    <circle cx="762" cy="341" r="31"/>
  </g>
  <g class="sans" font-size="20" font-weight="700" fill="var(--ink)" text-anchor="middle">
    <text x="584" y="190">25%</text>
    <text x="762" y="190">50%</text>
    <text x="584" y="348">75%</text>
    <text x="762" y="348">100%</text>
  </g>
  <g class="sans" font-size="12" fill="#444" text-anchor="middle">
    <text x="584" y="250">Lorem ipsum dolor sit amet,</text>
    <text x="584" y="267">consectetur adipiscing</text>
    <text x="762" y="250">Lorem ipsum dolor sit amet,</text>
    <text x="762" y="267">consectetur adipiscing</text>
    <text x="584" y="408">Lorem ipsum dolor sit amet,</text>
    <text x="584" y="425">consectetur adipiscing</text>
    <text x="762" y="408">Lorem ipsum dolor sit amet,</text>
    <text x="762" y="425">consectetur adipiscing</text>
  </g>

  <use href="#footer" x="0" y="482" width="916" height="33"/>
  <text x="86" y="502" class="foot">© Copyrights 2024 | All Rights Reserved</text>
  <text x="774" y="502" class="foot">Page No : 06</text>
</svg>

</body>
</html>
```